Modern Business Card for Larkwell 2018

Our company assumes the best about people. We are creating an online community of entrepreneurs and business leaders who struggle with marketing their business online.

This business card should POP! We recently got a new logo and are launching a new website next month, so our business cards should make a statement that feels:
-Fresh
-Smart
-Trustworthy
-Fun

Target Market(s)

small business owners, entrepreneurs

Industry/Entity Type

Digital Marketing

Contact Information for Business Card

Dimensions: 3.5" x 2"

Font styles to use
Sans Serif

Colors
f37122
ffffff

Requirements
Must have
• We need a business card with a modern, bold design. We will use one side of the card as a lead-generation offer, so text on one side will need to fit up to 140 characters. The business card should stick to our core colors (orange, black, and white).
Nice to have
• We think a vertical "portrait" design could be interesting.
Should not have
• Should not look like a traditional business card. The round icon should stand out from a distance.

```html
<!DOCTYPE html>
<html lang="en">
<head>
<meta charset="utf-8">
<title>Larkwell Business Card</title>
<link rel="stylesheet" href="https://fonts.googleapis.com/css2?family=Montserrat:wght@600;700;800&family=Open+Sans:wght@600;700&family=Permanent+Marker&family=Kalam:wght@400&display=swap">
<style>
  :root {
    --orange: #f37122;
    --orange-soft: #f58d4e;
    --ink: #2b2b2b;
    --white: #ffffff;
    --stage: #3a3a3c;
    --map-grey: #d4d4d4;
  }
  * { box-sizing: border-box; margin: 0; padding: 0; }
  html, body { width: 1200px; height: 900px; overflow: hidden; }
  body {
    background: var(--stage);
    position: relative;
    font-family: "Open Sans", sans-serif;
  }
  .card {
    position: absolute;
    top: 135px;
    width: 360px;
    height: 630px;
    background: var(--white);
    overflow: hidden;
    box-shadow: 0 14px 30px rgba(0,0,0,.45);
  }
  .card--offer { left: 190px; }
  .card--contact { left: 650px; }

  /* Offer side */
  .benefits {
    position: absolute; inset: 0 0 auto 0; height: 230px;
    background: var(--ink);
    padding: 52px 0 0 30px;
  }
  .benefit {
    display: flex; align-items: center; gap: 16px;
    height: 46px;
    color: var(--orange);
    font-family: "Montserrat", sans-serif;
    font-weight: 600; font-size: 17px; letter-spacing: 1.6px;
    text-transform: uppercase;
  }
  .benefit svg { width: 30px; height: 30px; flex: none; }
  .fold { position: absolute; left: 0; top: 205px; width: 360px; height: 60px; }
  .side-band { position: absolute; top: 270px; width: 20px; height: 200px; background: var(--orange); }
  .side-band--left { left: 0; }
  .side-band--right { right: 0; }
  .offer-box {
    position: absolute; left: 38px; top: 282px; width: 284px; height: 168px;
    background: var(--ink);
    border: 4px solid var(--orange);
    border-radius: 24px;
    padding: 18px 16px 0;
    color: var(--white);
    text-align: center;
    font-size: 15px; line-height: 1.35; font-weight: 600;
  }
  .offer-url {
    position: absolute; left: -4px; right: -4px; bottom: -4px; height: 48px;
    background: var(--white);
    border: 4px solid var(--orange);
    border-radius: 24px;
    display: flex; align-items: center; gap: 10px; padding-left: 14px;
    color: var(--ink); font-size: 14px; font-weight: 700;
  }
  .offer-url svg { width: 24px; height: 24px; flex: none; }
  .brand-panel {
    position: absolute; left: 0; right: 0; bottom: 0; height: 178px;
    background: var(--orange);
    display: flex; flex-direction: column; align-items: center; padding-top: 22px;
    color: var(--white);
  }
  .brand-mark { width: 56px; height: 56px; border-radius: 50%; background: var(--white); }
  .brand-name {
    margin-top: 12px;
    font-family: "Montserrat", sans-serif; font-weight: 800; font-size: 34px; letter-spacing: 1px;
  }
  .brand-tagline { font-family: "Kalam", cursive; font-size: 18px; margin-top: 2px; }

  /* Contact side */
  .map-area { position: absolute; background: var(--map-grey); opacity: .55; border-radius: 40px; }
  .map-area--top { left: 70px; top: 90px; width: 270px; height: 150px; }
  .map-area--bottom { left: 30px; top: 370px; width: 310px; height: 160px; }
  .contact {
    position: absolute; left: 0; right: 0; top: 250px;
    text-align: center; color: var(--ink);
  }
  .contact-role { font-family: "Montserrat", sans-serif; font-weight: 700; font-size: 13px; letter-spacing: .5px; }
  .contact-name { font-family: "Permanent Marker", cursive; font-size: 38px; margin: 4px 0 2px; }
  .contact-email { font-weight: 700; font-size: 16px; }
  .contact-mark { width: 30px; height: 30px; border-radius: 50%; background: var(--orange); margin: 18px auto 0; }
  .contact-band { position: absolute; left: 0; bottom: 0; width: 360px; height: 90px; }
</style>
</head>
<body>
  <section class="card card--offer">
    <div class="benefits">
      <div class="benefit">
        <svg viewBox="0 0 30 30"><circle cx="15" cy="7" r="4" fill="#f37122"/><circle cx="6" cy="20" r="4" fill="#f37122"/><circle cx="24" cy="20" r="4" fill="#f37122"/><path d="M15 11 L6 20 M15 11 L24 20 M6 20 H24" stroke="#f37122" stroke-width="2" fill="none"/></svg>
        Reach more people
      </div>
      <div class="benefit">
        <svg viewBox="0 0 30 30"><circle cx="15" cy="12" r="8" fill="none" stroke="#f37122" stroke-width="2.5"/><text x="15" y="16.5" text-anchor="middle" font-size="12" font-weight="700" fill="#f37122" font-family="Open Sans, sans-serif">$</text><rect x="4" y="23" width="22" height="4" rx="2" fill="#f37122"/></svg>
        Make more money
      </div>
      <div class="benefit">
        <svg viewBox="0 0 30 30"><circle cx="15" cy="9" r="5" fill="#f37122"/><circle cx="8" cy="21" r="5" fill="#f37122"/><circle cx="22" cy="21" r="5" fill="#f37122"/></svg>
        Create more impact
      </div>
    </div>
    <svg class="fold" viewBox="0 0 360 60" aria-hidden="true">
      <polygon points="0,30 360,0 360,25 0,60" fill="#f37122"/>
      <polygon points="0,30 20,38 20,60 0,60" fill="#c85a16"/>
    </svg>
    <div class="side-band side-band--left"></div>
    <div class="side-band side-band--right"></div>
    <div class="offer-box">
      <p>Get your free Larkwell Starter Package and our marketing guide today at</p>
      <div class="offer-url">
        <svg viewBox="0 0 24 24"><circle cx="12" cy="12" r="10" fill="none" stroke="#2b2b2b" stroke-width="1.8"/><ellipse cx="12" cy="12" rx="4.5" ry="10" fill="none" stroke="#2b2b2b" stroke-width="1.5"/><path d="M2 12 H22 M4 7 H20 M4 17 H20" stroke="#2b2b2b" stroke-width="1.5"/></svg>
        LARKWELLNOW.COM/START
      </div>
    </div>
    <div class="brand-panel">
      <div class="brand-mark"></div>
      <div class="brand-name">LARKWELL</div>
      <div class="brand-tagline">Tell Stories that inspire action</div>
    </div>
  </section>

  <section class="card card--contact">
    <div class="map-area map-area--top" role="img" aria-label="Dotted grey world map pattern"></div>
    <div class="map-area map-area--bottom" role="img" aria-label="Dotted grey world map pattern"></div>
    <div class="contact">
      <p class="contact-role">STORY MARKETING COACH</p>
      <p class="contact-name">DANA WHITFIELD</p>
      <p class="contact-email">dana@larkwellnow.com</p>
      <div class="contact-mark"></div>
    </div>
    <svg class="contact-band" viewBox="0 0 360 90" aria-hidden="true">
      <polygon points="0,90 360,40 360,90" fill="#f37122"/>
    </svg>
  </section>
</body>
</html>
```